Create a memorable Stationary for Security Software Company

Velbrantix is the worldwide leader in securing the Internet. Making Internet communications and critical data secure, reliable and available everywhere has been and continues to be our ongoing vision. We are committed to staying focused on real customer needs and to developing new and innovative security solutions that redefine the security landscape.

Industry/Entity Type

Internet

Font styles to use
Serif
Sans Serif
Script

Colors
0792cd
33a6d7
85cae6

```html
<!DOCTYPE html>
<html lang="en">
<head>
<meta charset="utf-8">
<title>Velbrantix Business Card</title>
<link href="https://fonts.googleapis.com/css2?family=Open+Sans:wght@400;600&display=swap" rel="stylesheet">
<style>
  :root {
    --bg: #e9e7e4;
    --card: #141414;
    --card-edge: #1e1e1e;
    --blue: #0792cd;
    --blue-mid: #33a6d7;
    --blue-light: #85cae6;
    --text: #f2f2f2;
  }
  * { margin: 0; padding: 0; box-sizing: border-box; }
  html, body { width: 1200px; height: 814px; overflow: hidden; }
  body {
    background: var(--bg);
    font-family: "Open Sans", Arial, sans-serif;
    position: relative;
  }
  .card {
    position: absolute;
    width: 520px;
    height: 300px;
    background: var(--card);
    border: 1px solid var(--card-edge);
    box-shadow: 0 6px 18px rgba(0,0,0,.25);
    top: 257px;
  }
  .card--front { left: 50px; }
  .card--back { left: 630px; }

  .brand {
    position: absolute;
    display: flex;
    align-items: center;
    gap: 10px;
    color: var(--blue-mid);
    font-weight: 600;
  }
  .brand__dot {
    border-radius: 50%;
    background: var(--blue-mid);
  }
  .card--front .brand { top: 34px; right: 34px; font-size: 24px; }
  .card--front .brand__dot { width: 22px; height: 22px; }

  .rule {
    position: absolute;
    left: 200px;
    right: 30px;
    top: 178px;
    height: 1px;
    background: var(--blue);
  }
  .address {
    position: absolute;
    right: 34px;
    top: 102px;
    text-align: right;
    color: var(--text);
    font-size: 14px;
    line-height: 20px;
  }
  .person {
    position: absolute;
    left: 34px;
    top: 164px;
  }
  .person__name {
    color: var(--blue);
    font-size: 19px;
    font-weight: 600;
    line-height: 24px;
  }
  .person__role {
    color: var(--text);
    font-size: 14px;
    line-height: 20px;
    margin-bottom: 4px;
  }
  .contact {
    list-style: none;
    color: var(--text);
    font-size: 14px;
    line-height: 21px;
  }
  .contact li { display: flex; align-items: center; gap: 10px; }
  .contact svg { width: 13px; height: 13px; fill: var(--blue-mid); flex: none; }

  .card--back .brand {
    left: 0; right: 0; top: 96px;
    justify-content: center;
    font-size: 40px;
    gap: 16px;
  }
  .card--back .brand__dot { width: 34px; height: 34px; }
  .website {
    position: absolute;
    left: 0; right: 0; top: 210px;
    text-align: center;
    color: var(--blue);
    font-size: 12px;
    letter-spacing: 5px;
  }
</style>
</head>
<body>

<section class="card card--front">
  <div class="brand"><span class="brand__dot"></span>Velbrantix</div>

  <address class="address">
    4120 Cedar Ridge Rd<br>
    Northvale, Oregon 97021<br>
    www.velbrantix.com
  </address>

  <div class="rule"></div>

  <div class="person">
    <div class="person__name">Mara Ellison</div>
    <div class="person__role">CEO/Founder</div>
    <ul class="contact">
      <li>
        <svg viewBox="0 0 24 24" aria-hidden="true"><path d="M6.6 10.8c1.4 2.8 3.8 5.1 6.6 6.6l2.2-2.2c.3-.3.7-.4 1-.2 1.1.4 2.3.6 3.6.6.6 0 1 .4 1 1V20c0 .6-.4 1-1 1C10.6 21 3 13.4 3 4c0-.6.4-1 1-1h3.5c.6 0 1 .4 1 1 0 1.3.2 2.5.6 3.6.1.3 0 .7-.2 1L6.6 10.8z"/></svg>
        555 210 7741
      </li>
      <li>
        <svg viewBox="0 0 24 24" aria-hidden="true"><path d="M7 3h10v5H7zM4 9h16a2 2 0 0 1 2 2v6h-4v4H6v-4H2v-6a2 2 0 0 1 2-2zm4 7v3h8v-3z"/></svg>
        555 318 4062
      </li>
      <li>
        <svg viewBox="0 0 24 24" aria-hidden="true"><path d="M2 5h20v14H2zm2 2v.5l8 5.5 8-5.5V7l-8 5.5z"/></svg>
        hello@velbrantix.com
      </li>
    </ul>
  </div>
</section>

<section class="card card--back">
  <div class="brand"><span class="brand__dot"></span>Velbrantix</div>
  <div class="website">www.velbrantix.com</div>
</section>

</body>
</html>
```